Under Morning Lantern website

I need a website to sell my t-shirt designs. I have around 5 designs I plan to sell on my initial launch, but only 3 photos at the moment. I would love a main page with the product images below maybe a large nicely designed header image, showing products with their sizes, item name/description, a way to add to cart and a review system like stars below each product image. Maybe a share option to Snapshots, Facepage, Chirper, Pinterest, etc. would be cool too. Also on the main page under the product images a section showcasing my Snapshots photos for the company. Then a section where I will include an About Me video from like YouTube. Lastly, on the main page an option to join my Mailing List at the footer with links to my Facepage and Snapshots social accounts, links to pages (About Me, Shop, Snapshots page, & Contact Us) as well as Track Order.

The other 4 pages will be for an About Me, which is the video I will make later that will be from YouTube. Then the Shop page. Then the Snapshots page showcasing all the photos I plan to use to market the products, and a Contact Us Page.

I plan to possibly connect this to Shopify, so showcasing payment options (Palo, Birch Pay, Wayfarer, etc.) would be nice.

Lastly, I don't plan on doing returns/exchanges so maybe an area showing that would be nice too. ALL SALES FINAL

Mobile Friendly!

1st image is logo and other 4 images are t-shirt designs

Coded - Design and coding required

5+ page

• Separate pages, No Refunds (All Sales Final), Add to Cart, Way to Purchase

```html
<!DOCTYPE html>
<html lang="en">
<head>
<meta charset="utf-8">
<title>Under Morning Lantern</title>
<link href="https://fonts.googleapis.com/css2?family=Poppins:wght@300;400;500;600;700;800&family=Montserrat:wght@400;500;600&display=swap" rel="stylesheet">
<style>
:root{
  --blue:#00a8ec;
  --grey-hero:#d5d8dd;
  --ink:#222831;
  --muted:#8a9099;
  --line:#e3e6ea;
  --star:#f5a623;
  --band:#e8f2fb;
  --soft:#f5f6f8;
  --footer:#333537;
  --shirt-black:#141414;
  --shirt-purple:#8a5cc4;
  --shirt-teal:#2fb3a6;
  --shirt-white:#e9eaec;
}
*{margin:0;padding:0;box-sizing:border-box}
html,body{width:1200px;height:3948px;overflow:hidden}
body{position:relative;font-family:"Poppins",sans-serif;color:var(--ink);background:#fff}
.abs{position:absolute}
.shape{position:absolute;border-radius:14px}

/* hero */
.hero-left{left:0;top:0;width:600px;height:676px;background:var(--blue)}
.hero-right{left:600px;top:0;width:600px;height:676px;background:var(--grey-hero)}
.logo{font-family:"Poppins",sans-serif;font-weight:800;font-size:44px;letter-spacing:1px;color:var(--ink);line-height:1}
.logo-sub{font-family:"Poppins",sans-serif;font-weight:700;font-size:8.5px;letter-spacing:3px;color:var(--ink)}
.nav{left:429px;top:49px;width:342px;height:38px;background:#fff;border-radius:19px;display:flex;align-items:center;justify-content:space-around;padding:0 22px;font-size:13px;color:#555}
.nav .active{color:var(--ink);font-weight:500;position:relative}
.nav .active::after{content:"";position:absolute;left:50%;bottom:-6px;width:3px;height:3px;border-radius:50%;background:var(--ink)}
.track{left:953px;top:59px;font-size:13px;color:#555}
.cart-badge{left:1066px;top:48px;width:14px;height:14px;border-radius:50%;background:var(--blue);color:#fff;font-size:9px;text-align:center;line-height:14px}
.hero-shirt{left:429px;top:153px;width:330px;height:368px;background:var(--shirt-black);border-radius:30px 30px 10px 10px}
.hero-title{left:0;width:1200px;top:320px;text-align:center;font-weight:700;font-size:96px;color:#fff;letter-spacing:-1px;line-height:1}
.hero-sub{left:0;width:1200px;top:428px;text-align:center;font-size:20px;color:#fff}
.item-name{left:176px;top:270px;font-size:16px;color:#fff;line-height:22px}
.dash{height:1px;width:43px;background:#fff}
.btn-outline-white{left:118px;top:363px;width:138px;height:38px;border:1.5px solid #fff;border-radius:19px;color:#fff;font-size:13px;font-weight:500;text-align:center;line-height:35px}
.color-label{left:933px;top:270px;font-size:16px;color:#444}
.size-row{left:116px;top:586px;display:flex;align-items:center;gap:8px;color:#fff;font-size:13px;font-weight:600}
.size{width:28px;height:28px;border:1.5px solid #fff;border-radius:50%;font-size:10px;font-weight:400;text-align:center;line-height:25px}
.size.on{background:#fff;color:var(--blue)}
.arrow-btn{top:579px;width:38px;height:37px;display:flex;align-items:center;justify-content:center}

/* tabs */
.tabs{left:0;width:1200px;top:748px;display:flex;justify-content:center;gap:54px;font-size:29px;font-weight:300;color:#9aa0a7}
.tabs .on{color:var(--ink);border-bottom:2px solid var(--ink);padding-bottom:4px}

/* product cards */
.card{width:221px;height:324px;border:1px solid var(--line);background:#fff}
.card.hover{background:#eef8fe;border-color:#9fd8f3}
.card .pic{position:absolute;left:30px;top:30px;width:160px;height:165px;border-radius:16px 16px 6px 6px}
.card .name{position:absolute;left:34px;top:226px;font-size:15px;font-weight:500}
.card .stars{position:absolute;left:34px;top:248px;font-size:12px;color:var(--star);letter-spacing:1px}
.card .price{position:absolute;left:34px;top:270px;font-size:17px;font-weight:600}
.tool{position:absolute;left:163px;width:38px;height:38px;border-radius:50%;border:1.5px solid var(--blue);background:#fff;display:flex;align-items:center;justify-content:center}
.tool.fill{background:var(--blue)}
.btn-blue{background:var(--blue);color:#fff;border-radius:20px;font-size:13px;font-weight:500;text-align:center}

/* promo */
.promo{left:0;top:1655px;width:1200px;height:377px;background:var(--band)}
.promo-title{left:560px;width:434px;text-align:center;top:1740px;font-size:33px;font-weight:500;color:#5b6470}

/* about */
.about{left:0;top:2032px;width:1200px;height:451px;background:var(--soft)}
.bubble{position:absolute;border-radius:50%;background:#e6e7ea}
.diamond{left:182px;top:2130px;width:274px;height:274px;background:var(--blue);border-radius:26px;transform:rotate(45deg)}
.note{position:absolute;background:#fff;border-radius:8px;box-shadow:0 6px 20px rgba(0,0,0,.06)}
.note i{position:absolute;border-radius:50%;background:#e4e6e9}
.note b{position:absolute;height:3px;background:#e6e8eb;border-radius:2px}
.watermark{left:602px;top:2065px;font-size:110px;font-weight:700;color:#eceef1;letter-spacing:12px;line-height:1}
.about-title{left:661px;top:2140px;font-size:30px;font-weight:600;color:#3a3f4c}
.about-title span{color:var(--blue)}
.about-lead{left:660px;top:2198px;width:420px;font-size:15px;font-weight:500;color:#4a505a;line-height:23px}
.about-text{left:660px;top:2262px;width:420px;font-family:"Montserrat",sans-serif;font-size:13px;color:#7a808a;line-height:23px}
.btn-outline{left:662px;top:2369px;width:115px;height:37px;border:1.5px solid #cfd3d8;border-radius:19px;font-size:13px;color:#555;display:flex;align-items:center;justify-content:center;gap:8px;background:#fff}

/* video */
.video{left:192px;top:2553px;width:816px;height:460px;background:linear-gradient(90deg,#5b5a60 0%,#6d5a86 40%,#2f6e68 70%,#7d7a6c 100%)}
.side-block{top:2703px;height:163px;background:#eef0f2}
.video-title{left:395px;top:2595px;font-size:25px;color:#fff}
.video-brand{left:240px;top:2593px;font-size:30px;font-weight:700;color:rgba(255,255,255,.25);letter-spacing:2px}
.play{left:570px;top:2721px;width:64px;height:64px;border-radius:50%;background:rgba(255,255,255,.85)}
.controls{left:192px;top:2972px;width:816px;height:41px;background:rgba(0,0,0,.55);display:flex;align-items:center;padding:0 18px;gap:14px;color:#fff;font-size:11px}
.track-bar{flex:1;height:3px;background:rgba(255,255,255,.3);position:relative}
.track-bar::before{content:"";position:absolute;left:0;top:0;width:22%;height:3px;background:#fff}

/* gallery */
.gallery-title{left:273px;top:3062px;font-size:31px;font-weight:700;color:#3a3f4c}
.gallery-text{left:273px;top:3110px;width:680px;font-size:15px;color:#333;line-height:22px}
.tile{position:absolute}

/* newsletter */
.news-title{left:0;width:1200px;text-align:center;top:3520px;font-size:33px;font-weight:400;color:#222}
.news-sub{left:0;width:1200px;text-align:center;top:3572px;font-size:11.5px;color:#666}
.news-field{left:261px;top:3626px;width:677px;height:24px;border-bottom:1px solid #ddd;font-size:10px;color:#aaa;display:flex;justify-content:space-between;align-items:center}

/* footer */
.footer{left:0;top:3703px;width:1200px;height:245px;background:var(--footer)}
.foot-head{font-size:15px;color:#fff}
.foot-text{font-size:13px;color:#b9bcc0;line-height:25px}
.foot-rule{top:3748px;width:1px;height:160px;background:#45484b}
.social{top:3845px;display:flex;gap:12px}
.social i{width:14px;height:14px;border-radius:50%;background:#9ea2a7;display:block}
</style>
</head>
<body>

<!-- hero -->
<div class="abs hero-left"></div>
<div class="abs hero-right"></div>
<div class="abs" style="left:118px;top:42px">
  <div class="logo">U.M.L.</div>
  <div class="logo-sub" style="margin-top:6px">UNDER MORNING LANTERN</div>
</div>
<nav class="abs nav"><span class="active">About</span><span>Shop</span><span>Snapshots</span><span>Contact</span></nav>
<div class="abs track">Track Order</div>
<svg class="abs" style="left:1048px;top:56px" width="26" height="24" viewBox="0 0 26 24" fill="none" stroke="#6b7078" stroke-width="1.6"><path d="M1 2h4l3 13h13l3-9H7"/><circle cx="10" cy="20" r="1.8"/><circle cx="19" cy="20" r="1.8"/></svg>
<div class="abs cart-badge">0</div>
<div class="abs hero-shirt" role="img" aria-label="Black half sleeve t-shirt with printed slogan"></div>
<div class="abs hero-title">Colorblack</div>
<div class="abs hero-sub">Half sleeve t-shirt</div>
<div class="abs dash" style="left:118px;top:280px"></div>
<div class="abs item-name">Product<br>Item Name</div>
<div class="abs btn-outline-white">Shop Now</div>
<div class="abs color-label">Color : Black</div>
<div class="abs dash" style="left:1040px;top:280px;background:#555"></div>
<div class="abs size-row">Size:<span class="dash" style="width:28px;margin-right:10px"></span>
  <span class="size">S</span><span class="size on">M</span><span class="size">L</span><span class="size">XL</span></div>
<div class="abs arrow-btn" style="left:995px;background:var(--blue)"><svg width="10" height="12" viewBox="0 0 10 12" fill="none" stroke="#fff" stroke-width="1.6"><path d="M7 1L2 6l5 5"/></svg></div>
<div class="abs arrow-btn" style="left:1045px;background:#b4bac2"><svg width="10" height="12" viewBox="0 0 10 12" fill="none" stroke="#fff" stroke-width="1.6"><path d="M3 1l5 5-5 5"/></svg></div>

<!-- tabs -->
<div class="abs tabs"><span class="on">New Arrival</span><span>Sale Off</span><span>Best Selling</span></div>

<!-- product grid -->
<div class="abs card" style="left:120px;top:840px"><div class="pic" role="img" aria-label="Black t-shirt with blue slogan print" style="background:var(--shirt-black)"></div><div class="name">Product Name</div><div class="stars">★★★☆☆</div><div class="price">$120.00</div></div>
<div class="abs card hover" style="left:366px;top:840px"><div class="pic" role="img" aria-label="Black t-shirt with blue logo print" style="background:var(--shirt-black)"></div>
  <div class="tool" style="top:24px"><svg width="16" height="16" viewBox="0 0 16 16" fill="none" stroke="#00a8ec" stroke-width="1.4"><path d="M2 6V2h4M10 2h4v4M14 10v4h-4M6 14H2v-4M2 2l4 4M14 2l-4 4M14 14l-4-4M2 14l4-4"/></svg></div>
  <div class="tool" style="top:78px"><svg width="16" height="15" viewBox="0 0 16 15" fill="none" stroke="#00a8ec" stroke-width="1.4"><path d="M8 14S1 9.5 1 5a3.5 3.5 0 0 1 7-1 3.5 3.5 0 0 1 7 1c0 4.5-7 9-7 9z"/></svg></div>
  <div class="tool fill" style="top:132px"><svg width="16" height="15" viewBox="0 0 16 15" fill="none" stroke="#fff" stroke-width="1.4"><path d="M1 1h2.5l2 8h8l1.5-5.5H4.5"/><circle cx="6.5" cy="12.5" r="1"/><circle cx="12" cy="12.5" r="1"/></svg></div>
  <div class="name">Product Name</div><div class="stars">★★★★☆</div><div class="price">$120.00</div></div>
<div class="abs card" style="left:613px;top:840px"><div class="pic" role="img" aria-label="Two white t-shirts, front and back view" style="background:var(--shirt-white)"></div><div class="name">Product Name</div><div class="stars">★★★★★</div><div class="price">$120.00</div></div>
<div class="abs card" style="left:860px;top:840px"><div class="pic" role="img" aria-label="Black t-shirt with purple logo print" style="background:var(--shirt-black)"></div><div class="name">Product Name</div><div class="stars">★★★★☆</div><div class="price">$120.00</div></div>

<div class="abs card" style="left:120px;top:1191px"><div class="pic" role="img" aria-label="Black and white t-shirts pair" style="background:linear-gradient(90deg,var(--shirt-black) 50%,var(--shirt-white) 50%)"></div><div class="name">Product Name</div><div class="stars">★★★★☆</div><div class="price">$120.00</div></div>
<div class="abs card" style="left:366px;top:1191px"><div class="pic" role="img" aria-label="Teal t-shirt with slogan print" style="background:var(--shirt-teal)"></div><div class="name">Product Name</div><div class="stars">★★★★☆</div><div class="price">$120.00</div></div>
<div class="abs card" style="left:613px;top:1191px"><div class="pic" role="img" aria-label="Black and purple t-shirts pair" style="background:linear-gradient(90deg,var(--shirt-black) 50%,var(--shirt-purple) 50%)"></div><div class="name">Product Name</div><div class="stars">★★★★☆</div><div class="price">$120.00</div></div>
<div class="abs card" style="left:860px;top:1191px"><div class="pic" role="img" aria-label="Black t-shirt with blue logo print" style="background:var(--shirt-black)"></div><div class="name">Product Name</div><div class="stars">★★★★☆</div><div class="price">$120.00</div></div>

<div class="abs btn-blue" style="left:543px;top:1551px;width:114px;height:40px;line-height:40px">More &nbsp;›</div>

<!-- promo -->
<div class="abs promo"></div>
<div class="abs shape" role="img" aria-label="Purple and teal t-shirts displayed together" style="left:200px;top:1683px;width:321px;height:300px;background:linear-gradient(135deg,var(--shirt-purple) 0%,var(--shirt-purple) 50%,var(--shirt-teal) 50%,var(--shirt-teal) 100%);border-radius:30px 30px 12px 12px"></div>
<div class="abs promo-title">Product Name</div>
<div class="abs" style="left:560px;width:434px;text-align:center;top:1793px;font-size:13px;color:var(--star);letter-spacing:2px">★★★★★</div>
<div class="abs" style="left:560px;width:434px;text-align:center;top:1817px;font-size:30px;font-weight:500">Only $99.00</div>
<div class="abs btn-blue" style="left:707px;top:1884px;width:139px;height:38px;line-height:38px">Quick Buy</div>

<!-- about -->
<div class="abs about"></div>
<div class="bubble" style="left:48px;top:2116px;width:48px;height:48px"></div>
<div class="bubble" style="left:70px;top:2288px;width:68px;height:68px"></div>
<div class="bubble" style="left:40px;top:2235px;width:12px;height:12px"></div>
<div class="bubble" style="left:93px;top:2383px;width:14px;height:14px"></div>
<div class="bubble" style="left:138px;top:2428px;width:26px;height:26px"></div>
<div class="bubble" style="left:268px;top:2092px;width:22px;height:22px"></div>
<div class="bubble" style="left:550px;top:2234px;width:70px;height:70px"></div>
<div class="bubble" style="left:592px;top:2424px;width:50px;height:50px"></div>
<div class="bubble" style="left:468px;top:2470px;width:28px;height:28px"></div>
<div class="abs diamond"></div>
<div class="note" style="left:282px;top:2128px;width:184px;height:62px"><i style="left:14px;top:15px;width:32px;height:32px"></i><b style="left:62px;top:22px;width:80px"></b><b style="left:62px;top:34px;width:100px"></b></div>
<div class="note" style="left:358px;top:2309px;width:186px;height:62px"><i style="left:14px;top:15px;width:32px;height:32px"></i><b style="left:62px;top:22px;width:80px"></b><b style="left:62px;top:34px;width:104px"></b></div>
<div class="abs" style="left:232px;top:2238px">
  <div class="logo" style="font-size:40px">U.M.L.</div>
  <div class="logo-sub" style="margin-top:4px;font-size:7.5px">UNDER MORNING LANTERN</div>
</div>
<div class="abs watermark">U.M.L.</div>
<div class="abs about-title">ABOUT <span>ME</span></div>
<div class="abs about-lead">Lorem Ipsum is simply dummy text of the printing and typesetting industry.</div>
<div class="abs about-text">Lorem Ipsum is simply dummy text of the printing and typesetting industry. Lorem Ipsum has been the industry's standard dummy text ever since the 1500s</div>
<div class="abs btn-outline">More <span>›</span></div>

<!-- video -->
<div class="abs side-block" style="left:0;width:166px"></div>
<div class="abs side-block" style="left:1030px;width:170px"></div>
<div class="abs video" role="img" aria-label="Video still of purple and teal t-shirts among flowers"></div>
<div class="abs video-brand">U.M.L.</div>
<div class="abs video-title">About UML Check out the video</div>
<div class="abs play"><svg width="64" height="64" viewBox="0 0 64 64"><path d="M26 20l18 12-18 12z" fill="#333"/></svg></div>
<div class="abs controls">
  <svg width="10" height="12" viewBox="0 0 10 12"><path d="M1 1l8 5-8 5z" fill="#fff"/></svg>
  <div class="track-bar"></div>
  <span>03:47 / 10:00</span>
  <svg width="14" height="12" viewBox="0 0 14 12"><path d="M1 4h3l4-3v10L4 8H1z" fill="#fff"/><path d="M10 3c1.5 1.5 1.5 4.5 0 6" stroke="#fff" fill="none"/></svg>
  <span style="color:var(--blue);font-weight:600">HD</span>
</div>

<!-- gallery -->
<div class="abs gallery-title">Snapshots</div>
<div class="abs gallery-text">Meet your fellow Humans! Show us your UML style on Chirper, Snapshots or Facepage and tag @UML for a chance to win free tees and be featured on our site!</div>
<div class="tile" role="img" aria-label="Purple t-shirt on dark backdrop" style="left:254px;top:3183px;width:318px;height:293px;background:#3d434c"></div>
<div class="abs" style="left:390px;top:3305px;width:44px;height:44px;border:3px solid rgba(255,255,255,.7);border-radius:50%"></div>
<div class="tile" role="img" aria-label="Customer photo outdoors on rocks" style="left:585px;top:3183px;width:177px;height:142px;background:linear-gradient(160deg,#7f8a8f,#4e5a60)"></div>
<div class="tile" role="img" aria-label="Customer in dark hoodie on field" style="left:774px;top:3183px;width:172px;height:142px;background:linear-gradient(160deg,#a8a69c,#5a564e)"></div>
<div class="tile" role="img" aria-label="Customer in white shirt by a wall" style="left:585px;top:3337px;width:177px;height:139px;background:linear-gradient(160deg,#4f5358,#8b8e92)"></div>
<div class="tile" role="img" aria-label="Customer sitting by the waterfront" style="left:774px;top:3337px;width:172px;height:139px;background:linear-gradient(160deg,#b9c6d2,#7b8792)"></div>

<!-- newsletter -->
<div class="abs news-title">Join Our Newsletter</div>
<div class="abs news-sub">Sale up to 20% off for your next purchase in this month!</div>
<div class="abs news-field"><span>Your email address</span><span>Subscribe</span></div>

<!-- footer -->
<div class="abs footer"></div>
<div class="abs" style="left:153px;top:3746px">
  <div class="foot-head">Contact Us</div>
  <div class="foot-text" style="margin-top:14px">Lorem Ipsum, is simply<br>dummy text of the</div>
  <div class="foot-text" style="margin-top:10px">+000 0000 00000</div>
  <div class="foot-text" style="margin-top:8px">hello@lanternmail.com</div>
</div>
<div class="abs foot-rule" style="left:402px"></div>
<div class="abs" style="left:530px;top:3746px">
  <div class="foot-head">Contact Us</div>
  <div class="foot-text" style="margin-top:14px;line-height:24.5px">Home<br>About<br>Services<br>Contact<br>Track Order</div>
</div>
<div class="abs foot-rule" style="left:734px"></div>
<div class="abs" style="left:874px;top:3772px">
  <div class="logo" style="font-size:31px;color:var(--blue)">U.M.L.</div>
  <div class="logo-sub" style="font-size:6px;color:#fff;margin-top:3px;letter-spacing:2px">UNDER MORNING LANTERN</div>
</div>
<div class="abs social" style="left:870px"><i></i><i></i><i></i><i></i><i></i></div>

</body>
</html>
```